Accountant services flyer & marketing portfolio

I require a design for a marketing portfolio of blank templates for a flyer, product brochure, report cover for A4 based on our style - current logo, letterhead, website look and feel - that can be updated in publisher or word with relevant marketing and company information editorial material and text. It will be either printed A4 or saved as PDF and distributed

Target Market(s)

small business and investment / superfund clients

Industry/Entity Type

Accountant

Font styles to use
Sans Serif

Requirements
Must have
• Instyle of letterhead and website
Professional body logos
Space to input text
Relevant happy images
Nice to have
• Images of happy lifestyle types retirees, young families and mid-aged
tradesmen and professionals

```html
<!DOCTYPE html>
<html lang="en">
<head>
<meta charset="utf-8">
<title>Larkfield Accounting – Letterhead Flyer</title>
<link href="https://fonts.googleapis.com/css2?family=Open+Sans:wght@400;600;700&family=Barlow+Semi+Condensed:wght@400;500&display=swap" rel="stylesheet">
<style>
  :root {
    --orange: #e8611c;
    --orange-light: #f2922a;
    --yellow: #f4b331;
    --ink: #111111;
    --paper: #ffffff;
    --photo-warm: #c98a5a;
    --photo-soft: #e9d9cc;
  }
  * { margin: 0; padding: 0; box-sizing: border-box; }
  html, body { width: 723px; height: 1200px; overflow: hidden; background: var(--paper); }
  .flyer {
    position: relative;
    width: 723px;
    height: 1200px;
    font-family: "Open Sans", Arial, sans-serif;
    color: var(--ink);
    overflow: hidden;
  }
  .flyer-shapes { position: absolute; inset: 0; }

  .brand {
    position: absolute;
    left: 34px;
    top: 128px;
    width: 290px;
  }
  .brand-mark {
    display: block;
    width: 34px;
    height: 34px;
    border-radius: 50%;
    background: var(--orange);
    margin: 0 0 10px 100px;
  }
  .brand-name {
    font-size: 24px;
    font-weight: 600;
    color: var(--orange);
    letter-spacing: -0.5px;
    line-height: 1.05;
    white-space: nowrap;
  }
  .brand-tagline {
    font-size: 17px;
    font-weight: 400;
    line-height: 1.2;
    letter-spacing: -0.3px;
    white-space: nowrap;
  }

  .letter-date {
    position: absolute;
    left: 36px;
    top: 303px;
    font-family: "Barlow Semi Condensed", "Arial Narrow", sans-serif;
    font-size: 37px;
    color: var(--paper);
    letter-spacing: 0.3px;
  }

  .salutation {
    position: absolute;
    left: 36px;
    top: 448px;
    font-size: 28px;
    line-height: 1.45;
  }
  .salutation strong { font-weight: 700; display: block; }

  .subject {
    position: absolute;
    left: 36px;
    top: 566px;
    font-size: 28px;
    font-weight: 700;
  }

  .letter-body {
    position: absolute;
    left: 36px;
    top: 620px;
    width: 652px;
    font-size: 14.4px;
    line-height: 23px;
    text-align: justify;
    letter-spacing: -0.2px;
  }
  .letter-body p + p { margin-top: 23px; }

  .sign-off {
    position: absolute;
    left: 36px;
    top: 973px;
    font-size: 19px;
    font-weight: 600;
  }
  .signature {
    position: absolute;
    left: 36px;
    top: 1010px;
    width: 190px;
    height: 110px;
    background: linear-gradient(135deg, #f4f4f4, #e6e6e6);
    border-radius: 4px;
  }
  .firm-role {
    position: absolute;
    left: 36px;
    top: 1136px;
    font-size: 19px;
    font-weight: 600;
  }

  .signatory {
    position: absolute;
    right: 35px;
    top: 975px;
    font-size: 24px;
    font-weight: 600;
    line-height: 1.45;
  }

  .web-address {
    position: absolute;
    right: 35px;
    top: 1146px;
    font-family: "Barlow Semi Condensed", "Arial Narrow", sans-serif;
    font-size: 28px;
    color: var(--paper);
  }
</style>
</head>
<body>
<main class="flyer">
  <svg class="flyer-shapes" width="723" height="1200" viewBox="0 0 723 1200">
    <defs>
      <radialGradient id="photoTone" cx="50%" cy="45%" r="60%">
        <stop offset="0%" stop-color="#e9d9cc" />
        <stop offset="100%" stop-color="#c98a5a" />
      </radialGradient>
    </defs>

    <path class="date-band" fill="var(--orange)"
      d="M0,265 L340,265 C330,330 355,395 430,440 C330,400 170,385 0,450 Z"/>
    <path class="date-band-accent" fill="var(--orange-light)"
      d="M0,450 C170,385 330,400 430,440 C320,420 160,425 0,475 Z"/>

    <ellipse class="hero-photo" cx="580" cy="275" rx="225" ry="228" fill="url(#photoTone)"
      role="img" aria-label="Photo of a smiling young family sharing a laptop on a sofa"/>

    <path class="photo-arc" fill="var(--yellow)"
      d="M560,0 C385,40 305,200 325,330 C348,455 455,525 605,520 C665,518 700,500 723,478 L723,455 C640,500 520,478 465,405 C395,315 420,115 560,0 Z"/>
    <path class="photo-arc-inner" fill="var(--orange-light)"
      d="M723,400 C700,450 640,480 570,478 C640,470 690,440 723,380 Z"/>
    <path class="photo-arc-top" fill="var(--orange)"
      d="M600,0 C670,8 705,35 723,62 L723,28 C700,10 680,3 660,0 Z"/>

    <path class="footer-accent" fill="var(--orange-light)"
      d="M250,1200 C420,1125 560,1085 723,1072 L723,1098 C560,1108 420,1155 335,1200 Z"/>
    <path class="footer-band" fill="var(--orange)"
      d="M300,1200 C440,1140 580,1104 723,1094 L723,1200 Z"/>
    <path class="footer-corner" fill="var(--orange)"
      d="M0,1172 C20,1182 40,1192 60,1200 L0,1200 Z"/>
  </svg>

  <header class="brand">
    <span class="brand-mark"></span>
    <div class="brand-name">LARKFIELD ACCOUNTING</div>
    <div class="brand-tagline">Clear numbers. Calm decisions</div>
  </header>

  <div class="letter-date">23 NOVEMBER 2020</div>

  <div class="salutation">
    <strong>Dear,</strong>
    Lorem Ipsum
  </div>

  <div class="subject">RE:</div>

  <section class="letter-body">
    <p>Lorem Ipsum is simply dummy text of the printing and typesetting industry. Lorem Ipsum has been the industry's standard dummy text ever since the 1500s, when an unknown printer took a galley of type and scrambled it to make a type specimen book. It has survived not only five centuries, but also the leap into electronic typesetting, remaining essentially unchanged. It was popularised in the 1960s with the release of Letraset sheets containing Lorem Ipsum passages, and more recently with desktop publishing software like Aldus PageMaker including versions of Lorem Ipsum.</p>
    <p>Lorem Ipsum is simply dummy text of the printing and typesetting industry. Lorem Ipsum has been the industry's standard dummy text ever since the 1500s, when an unknown printer took a galley of type and scrambled it to make a type specimen book. It has survived not only five centuries, but also the leap into electronic typesetting, remaining essentially unchanged. It was popularised in the 1960s with the release of Letraset sheets containing Lorem Ipsum passages, and more recently with desktop publishing software like Aldus PageMaker including versions of Lorem Ipsum.</p>
  </section>

  <div class="sign-off">Kindest Regards</div>
  <div class="signature" role="img" aria-label="Handwritten signature"></div>
  <div class="firm-role">Chartered Accountants</div>

  <div class="signatory">
    Daniel Harper<br>
    CEO and Founder
  </div>

  <div class="web-address">www.larkfieldaccounting.com.au</div>
</main>
</body>
</html>
```